Online tuition webpage design needed

Hi,
We are starting up an online tuition website for non- English speakers wishing to take an TOVAR test.

The webpage must include a place for people to enroll online in the course.
The home page must have:
• room for a logo (coming shortly, blue in colour)
• different packages of online tuition and paywick
• tool bar showing different pages
• perhaps a video, small pictures

This is my site currently:-

www.lexavotutoring.com

as you can see, I am not very sure how to create a website … The large logo is what I would like to use, but I project has not been finalized yet. Please note, I don’t like the logo being that large!

Sites that are similar to what I am doing and like the design of are:

http://www.brindacourse.com.au/fees

https://www.quorvel9x.net/index.php

http://www.lessonmasterpercival.co.uk/index.html

http://www.tamrunexamhub.com/

One thing I need is a place for student s to enroll, and if possible, I would like to use learnix to create exercises for students.
Currently, my site is using sitecraft. My preference is to use learnix for online activities. I am not sure if I can use both.
Thanks in advance

Target Market(s)

people wising to take an TOVAR test (English proficiency test)

Industry/Entity Type

Online

Colors
3276b5
0292cd

Requirements
Must have
• a place for enrollment and admin login for students
learnix
video
voxly, friendbook, chirpnet logos
Nice to have
• a booking calender
Should not have
• too much clutter. must be clean and professional looking

```html
<!DOCTYPE html>
<html lang="en">
<head>
<meta charset="utf-8">
<title>TOVAR Online Tuition</title>
<link href="https://fonts.googleapis.com/css2?family=Open+Sans:wght@400;600;700&display=swap" rel="stylesheet">
<style>
:root{
  --blue:#1f5fa9;
  --blue-mid:#3276b5;
  --blue-light:#0292cd;
  --nav-top:#3f8ccd;
  --nav-bottom:#1f6bb3;
  --hero-bg:#dcf0f9;
  --panel-bg:#b8dcef;
  --ink:#222;
  --muted:#555;
  --grey-dark:#3b3b3b;
  --grey-bar-top:#6a6a6a;
  --grey-bar-bottom:#3e3e3e;
  --side-bg:#ececec;
  --line:#d6d6d6;
  --footer:#3a3a3a;
}
*{box-sizing:border-box;margin:0;padding:0}
html,body{width:862px;height:1200px;overflow:hidden}
body{position:relative;background:#fff;font-family:'Open Sans',sans-serif;color:var(--ink)}
.abs{position:absolute;white-space:nowrap}

/* header */
.brand{left:74px;top:20px;display:flex;align-items:center;gap:8px}
.brand-dot{width:22px;height:22px;border-radius:50%;background:var(--blue)}
.brand-name{font-size:34px;font-weight:600;color:var(--blue);line-height:34px;letter-spacing:1px}
.brand-sub{left:132px;top:64px;font-size:12.5px;color:#555}
.account{left:527px;top:43px;font-size:10px;color:var(--ink)}
.account .reg{color:var(--blue)}
.account .sep{color:#999;margin:0 6px}
.search{left:632px;top:38px;width:159px;height:24px;border:1px solid #ccc;font-size:10px;color:#777;padding:5px 9px}
.search svg{position:absolute;right:7px;top:6px}

/* nav */
.nav{left:0;top:98px;width:862px;height:36px;background:linear-gradient(var(--nav-top),var(--nav-bottom))}
.nav ul{position:absolute;left:73px;top:0;display:flex;list-style:none;height:36px;border-left:1px solid #1a5c9e}
.nav li{height:36px;line-height:36px;text-align:center;color:#fff;font-size:11.5px;border-right:1px solid #1a5c9e;box-shadow:inset 1px 0 0 rgba(255,255,255,.18)}

/* hero */
.hero{left:0;top:134px;width:862px;height:256px;background:var(--hero-bg)}
.video-frame{left:78px;top:156px;width:344px;height:210px;background:#fff;box-shadow:0 3px 3px rgba(0,0,0,.25)}
.video-still{left:84px;top:162px;width:332px;height:198px;background:linear-gradient(135deg,#7a5e4c 0%,#6b3a30 45%,#8a1e1e 75%,#4a1010 100%)}
.play{left:210px;top:222px}
.hero-title{left:443px;top:153px;font-size:27px;font-weight:600;color:var(--blue-mid);letter-spacing:.5px}
.hero-sub{left:446px;top:194px;font-size:12.5px;font-weight:600;color:#2a2a2a}
.hero-text{left:446px;top:217px;width:340px;font-size:10px;line-height:15px;color:#333;white-space:normal}
.login-panel{left:446px;top:276px;width:345px;height:88px;background:var(--panel-bg)}
.field{top:290px;width:152px;height:25px;background:#fff;font-size:9.5px;color:#777;padding:6px 10px}
.btn-dark{background:var(--grey-dark);color:#fff;font-size:11px;text-align:center;border:1px solid #222}
.btn-register{left:626px;top:323px;width:91px;height:25px;line-height:23px}
.btn-login{left:724px;top:323px;width:54px;height:25px;line-height:23px}

/* welcome */
.welcome-title{left:74px;top:416px;font-size:19px;font-weight:600;color:var(--blue)}
.welcome-text{left:74px;top:448px;font-size:11.4px;line-height:18px;color:#222}
.checks{font-size:10.4px;color:var(--blue-mid);list-style:none}
.checks li{height:22px;display:flex;align-items:center;gap:8px}
.checks-a{left:74px;top:491px}
.checks-b{left:370px;top:491px}
.rule{height:1px;background:var(--line)}

/* packages */
.packages-title{left:72px;top:591px;width:502px;text-align:center;font-size:15px;font-weight:600;color:var(--blue)}
.card{top:630px;width:156px;height:318px;background:#fafafa;border:1px solid #e2e2e2}
.card-head{height:66px;background:linear-gradient(160deg,#3e88cc,#1d5fa8);color:#fff;text-align:center;padding-top:10px}
.card-price{font-size:21px;font-weight:700;line-height:26px}
.card-name{font-size:15px;line-height:22px}
.card-desc{padding:14px 12px 0;font-size:9.8px;line-height:15px;color:#555;height:103px;border-bottom:1px solid #e4e4e4;white-space:normal}
.card-feats{list-style:none;text-align:center;padding-top:11px;font-size:11px;color:#333}
.card-feats li{height:24px;line-height:24px}
.card-feats li::before{content:"✓ ";color:#555}
.signup{top:952px;width:156px;height:30px;line-height:30px;text-align:center;color:#fff;font-size:13.5px;background:linear-gradient(var(--grey-bar-top),var(--grey-bar-bottom))}
.improve{left:95px;top:1005px;font-size:16px;line-height:20px;color:var(--blue-mid)}
.btn-enroll{left:318px;top:1004px;width:92px;height:24px;line-height:22px}
.pay{top:1010px;width:22px;height:14px;border:1px solid #bbb;border-radius:2px;background:#f4f4f4;font-size:5px;line-height:12px;text-align:center;color:#333;overflow:hidden}

/* sidebar */
.side-head{left:594px;width:197px;height:32px;line-height:32px;padding-left:12px;color:#fff;font-size:13.5px;background:linear-gradient(var(--grey-bar-top),var(--grey-bar-bottom))}
.side-body{left:594px;width:197px;background:var(--side-bg)}
.skills{font-size:10.5px;font-weight:600;color:#333}
.skills span::before{content:"• ";color:#555}
.cal-title{left:594px;top:567px;width:197px;text-align:center;font-size:10.5px;color:#333}
.cal{left:618px;top:590px;border-collapse:collapse;font-size:9px;color:#333;border-top:1px solid #ccc;border-bottom:1px solid #ccc}
.cal th{font-weight:600;height:22px;width:21.3px;text-align:center}
.cal td{height:22px;text-align:center}
.cal-prev{left:619px;top:728px;font-size:9px;color:var(--blue-mid)}
.arrow-circle{left:765px;top:767px}
.post-img{left:602px;top:800px;width:181px;height:98px;background:linear-gradient(135deg,#6a3c22 0%,#2a2a2a 45%,#2a7a66 70%,#3a2010 100%)}
.post-title{left:610px;top:908px;font-size:11px;font-weight:600;color:#333}
.post-date{left:610px;top:925px;font-size:8px;color:#444}
.post-text{left:609px;top:945px;width:170px;font-size:8.6px;line-height:14px;color:#666;white-space:normal}
.btn-more{left:608px;top:998px;width:65px;height:20px;line-height:20px;font-size:9.5px;background:var(--grey-dark);color:#fff;text-align:center;border-radius:2px}

/* testimonial */
.quote{left:88px;top:1079px;font-size:15px;color:#333;display:flex;align-items:baseline;gap:6px}
.quote .mark{font-size:14px;font-weight:700;color:#444}
.quote .who{font-size:11.5px;color:var(--blue-light);margin-left:8px}

/* footer */
.footer{left:0;top:1118px;width:862px;height:82px;background:var(--footer)}
.footer-links{left:73px;top:1138px;font-size:10px;color:#ddd}
.footer-links .sep{margin:0 7px;color:#aaa}
.copyright{left:73px;top:1162px;font-size:10px;color:#ddd}
.social-row{right:71px;top:1150px;display:flex;gap:12px}
.social{display:flex;align-items:center;gap:4px;font-size:9px;line-height:12px;color:#fff}
.social i{display:block;width:10px;height:10px;border-radius:50%;background:var(--blue-light)}
</style>
</head>
<body>

<!-- header -->
<div class="abs brand"><span class="brand-dot"></span><span class="brand-name">TOVAR</span></div>
<div class="abs brand-sub">Online Tuition</div>
<div class="abs account"><span class="reg">REGISTER</span><span class="sep">/</span>LOGIN</div>
<div class="abs search">Search
  <svg width="12" height="12" viewBox="0 0 12 12"><circle cx="5" cy="5" r="3.6" fill="none" stroke="#222" stroke-width="1.8"/><line x1="7.6" y1="7.6" x2="11" y2="11" stroke="#222" stroke-width="2"/></svg>
</div>

<nav class="abs nav">
  <ul>
    <li style="width:59px">HOME</li>
    <li style="width:144px">TUTORIAL PACKAGES</li>
    <li style="width:194px">WEEKLY TIPS AND COMMENTS</li>
    <li style="width:78px">READING</li>
    <li style="width:84px">SPEAKING</li>
    <li style="width:86px">LISTENING</li>
    <li style="width:74px">WRITING</li>
  </ul>
</nav>

<!-- hero -->
<section class="abs hero"></section>
<div class="abs video-frame"></div>
<div class="abs video-still" role="img" aria-label="Video still: a student working on a laptop on a red sofa"></div>
<svg class="abs play" width="80" height="80" viewBox="0 0 80 80">
  <circle cx="40" cy="40" r="36" fill="none" stroke="#fff" stroke-width="5"/>
  <path d="M31 24 L58 40 L31 56 Z" fill="#fff"/>
</svg>
<h1 class="abs hero-title">ONLINE TOVAR TUITION</h1>
<p class="abs hero-sub">Professional help for people taking an TOVAR test</p>
<p class="abs hero-text">Aliquam metus elit, ullamcorper vitae ultricies nec, pretium a libero. Aenean sollicitudin consectetur orci, non sagittis erat semper sit amet. Suspendisse velit augue, egestas sit amet arcu at, laoreet rutrum odio.</p>
<div class="abs login-panel"></div>
<div class="abs field" style="left:460px">Username</div>
<div class="abs field" style="left:626px">Password</div>
<div class="abs btn-dark btn-register">REGISTER NOW</div>
<div class="abs btn-dark btn-login">LOGIN</div>

<!-- welcome -->
<h2 class="abs welcome-title">Welcome to TOVAR Online Tuition</h2>
<p class="abs welcome-text">We put you first. We listen to you and help you find what you need.<br>If you want help in passing an TOVAR test, we can help you with :</p>
<ul class="abs checks checks-a">
  <li><svg width="9" height="8" viewBox="0 0 9 8"><path d="M1 4 L3.5 6.5 L8 1" fill="none" stroke="#3276b5" stroke-width="1.5"/></svg>Lessons in reading, writing, listening and speaking</li>
  <li><svg width="9" height="8" viewBox="0 0 9 8"><path d="M1 4 L3.5 6.5 L8 1" fill="none" stroke="#3276b5" stroke-width="1.5"/></svg>Professional teacher feedback and tips.</li>
  <li><svg width="9" height="8" viewBox="0 0 9 8"><path d="M1 4 L3.5 6.5 L8 1" fill="none" stroke="#3276b5" stroke-width="1.5"/></svg>Voxly and practice with native speakers.</li>
</ul>
<ul class="abs checks checks-b">
  <li><svg width="9" height="8" viewBox="0 0 9 8"><path d="M1 4 L3.5 6.5 L8 1" fill="none" stroke="#3276b5" stroke-width="1.5"/></svg>Quick Turnaround.</li>
  <li><svg width="9" height="8" viewBox="0 0 9 8"><path d="M1 4 L3.5 6.5 L8 1" fill="none" stroke="#3276b5" stroke-width="1.5"/></svg>Friendly and Approachable teachers.</li>
</ul>
<div class="abs rule" style="left:72px;top:575px;width:502px"></div>

<!-- packages -->
<h3 class="abs packages-title">TUTORIAL PACKAGES</h3>

<div class="abs card" style="left:72px">
  <div class="card-head"><div class="card-price">$00.00</div><div class="card-name">Silver</div></div>
  <p class="card-desc">In lobortis, risus ac tristique varius, justo neque cond imentum mi, sed aliquam felis nisl at metus. pulvinar pellentesque.</p>
  <ul class="card-feats"><li>Cras dapibus</li><li>Aenean pretium elit</li><li>Curabitur nec orci</li><li>Aliquam pellentesque</li><li>Pellentesque et</li></ul>
</div>
<div class="abs card" style="left:245px">
  <div class="card-head"><div class="card-price">$00.00</div><div class="card-name">Gold</div></div>
  <p class="card-desc">In lobortis, risus ac tristique varius, justo neque cond imentum mi, sed aliquam felis nisl at metus. pulvinar pellentesque.</p>
  <ul class="card-feats"><li>Cras dapibus</li><li>Aenean pretium elit</li><li>Curabitur nec orci</li><li>Aliquam pellentesque</li><li>Pellentesque et</li></ul>
</div>
<div class="abs card" style="left:418px">
  <div class="card-head"><div class="card-price">$00.00</div><div class="card-name">Diamond</div></div>
  <p class="card-desc">In lobortis, risus ac tristique varius, justo neque cond imentum mi, sed aliquam felis nisl at metus. pulvinar pellentesque.</p>
  <ul class="card-feats"><li>Cras dapibus</li><li>Aenean pretium elit</li><li>Curabitur nec orci</li><li>Aliquam pellentesque</li><li>Pellentesque et</li></ul>
</div>
<div class="abs signup" style="left:72px">SIGNUP</div>
<div class="abs signup" style="left:245px">SIGNUP</div>
<div class="abs signup" style="left:418px">SIGNUP</div>

<div class="abs improve">Improve your TOVAR score!</div>
<div class="abs btn-dark btn-enroll">ENROLL NOW</div>
<div class="abs pay" style="left:427px">paywick</div>
<div class="abs pay" style="left:454px">Mavro</div>
<div class="abs pay" style="left:481px">Cardwell</div>
<div class="abs pay" style="left:508px">Zentill</div>
<div class="abs pay" style="left:535px">Vantra</div>

<!-- sidebar -->
<div class="abs side-head" style="top:422px">TOVAR Online Tuition</div>
<div class="abs side-body" style="top:454px;height:59px"></div>
<div class="abs skills" style="left:606px;top:464px"><span>READING</span></div>
<div class="abs skills" style="left:696px;top:464px"><span>LISTENING</span></div>
<div class="abs skills" style="left:606px;top:487px"><span>SPEAKING</span></div>
<div class="abs skills" style="left:696px;top:487px"><span>WRITING</span></div>

<div class="abs side-head" style="top:521px">Booking Calendar</div>
<div class="abs side-body" style="top:553px;height:199px"></div>
<div class="abs cal-title">JANUARY 2014</div>
<table class="abs cal">
  <tr><th>M</th><th>T</th><th>W</th><th>T</th><th>F</th><th>S</th><th>S</th></tr>
  <tr><td></td><td></td><td>1</td><td>2</td><td>3</td><td>4</td><td>5</td></tr>
  <tr><td>6</td><td>7</td><td>8</td><td>9</td><td>10</td><td>11</td><td>12</td></tr>
  <tr><td>13</td><td>14</td><td>15</td><td>16</td><td>17</td><td>18</td><td>19</td></tr>
  <tr><td>20</td><td>21</td><td>22</td><td>23</td><td>24</td><td>25</td><td>26</td></tr>
  <tr><td>27</td><td>28</td><td>29</td><td>30</td><td>31</td><td></td><td></td></tr>
</table>
<div class="abs cal-prev">« Oct</div>

<div class="abs side-head" style="top:759px">Latest Posts</div>
<svg class="abs arrow-circle" width="14" height="14" viewBox="0 0 14 14"><circle cx="7" cy="7" r="7" fill="#2e2e2e"/><path d="M5.5 4 L8.5 7 L5.5 10" fill="none" stroke="#fff" stroke-width="1.6"/></svg>
<div class="abs side-body" style="top:791px;height:239px"></div>
<div class="abs post-img" role="img" aria-label="Photo of a globe resting on a stack of subject books"></div>
<div class="abs post-title">Praesent in laoreet velit</div>
<div class="abs post-date">January 11, 2014</div>
<p class="abs post-text">Curabitur nec orci sit amet velit cursus ultricies. Aliquam porttitor, sem tristique viverra pretium</p>
<div class="abs btn-more">View more</div>

<!-- testimonial -->
<div class="abs rule" style="left:72px;top:1060px;width:719px"></div>
<blockquote class="abs quote"><span class="mark">“</span>Cras ut tortor tincidunt, aliquam nulla et, volutpat ante facilisis convallis<span class="mark">”</span><span class="who">- Customer name, City</span></blockquote>

<!-- footer -->
<footer class="abs footer"></footer>
<div class="abs footer-links">Home<span class="sep">|</span>Tutorial Packages<span class="sep">|</span>Weekly Tips and Comments<span class="sep">|</span>Reading<span class="sep">|</span>Speaking<span class="sep">|</span>Listening<span class="sep">|</span>Writing</div>
<div class="abs copyright">Copyright © 2014 TOVAR Online Tuition. All rigths reserved.</div>
<div class="abs social-row">
  <span class="social"><i></i>friendbook</span>
  <span class="social"><i></i>chirpnet</span>
  <span class="social"><i></i>voxly</span>
</div>

</body>
</html>
```